Executive Business Card for Healthcare Company [Need Today]

I need a business card design for a healthcare company. The only branding the company has thus far is a logo. The cards will be utilized by company executives. The design I envision will be vibrant and appealing but with a corporate feel. They shouldn't be too casual or playful. I would like to complete this project TODAY if possible.

Target Market(s)

Healthcare vendors, other executives in healthcare and pharmaceuticals

Industry/Entity Type

Pharmaceutical

Contact Information for Business Card

See attachment

Font styles to use
Serif
Sans Serif

Colors

Designer to choose colors to be used in the design.

```html
<!DOCTYPE html>
<html lang="en">
<head>
<meta charset="utf-8">
<title>Corvane Therapeutics — Business Card</title>
<link href="https://fonts.googleapis.com/css2?family=Arimo:wght@400;700&display=swap" rel="stylesheet">
<style>
  :root {
    --backdrop: #242424;
    --card-white: #ffffff;
    --teal: #35bcc6;
    --green: #5cc08f;
    --ink: #1d1d1d;
    --divider: #c9c9c9;
    --icon-fill: #e6f7f7;
  }
  html, body {
    margin: 0;
    padding: 0;
    width: 1200px;
    height: 900px;
    overflow: hidden;
    background: var(--backdrop);
    font-family: "Arimo", Arial, sans-serif;
  }
  .canvas { position: relative; width: 1200px; height: 900px; }
  .card {
    position: absolute;
    top: 306px;
    width: 439px;
    height: 271px;
    border-radius: 10px;
    overflow: hidden;
  }
  .card-front { left: 149px; background: var(--card-white); }
  .card-back { left: 609px; }

  .brand {
    position: absolute;
    left: 40px;
    top: 66px;
    width: 150px;
    text-align: center;
  }
  .brand-circle {
    display: block;
    width: 72px;
    height: 72px;
    margin: 0 auto 12px;
    border: 3px solid var(--green);
    border-radius: 50%;
    box-sizing: border-box;
  }
  .brand-name {
    margin: 0;
    color: var(--teal);
    font-weight: 400;
    font-size: 17px;
    line-height: 1.15;
    letter-spacing: 0.5px;
  }

  .divider {
    position: absolute;
    left: 211px;
    top: 62px;
    width: 1px;
    height: 142px;
    background: var(--divider);
  }

  .contact {
    position: absolute;
    left: 233px;
    top: 64px;
    color: var(--ink);
  }
  .person-name {
    margin: 0;
    font-size: 16px;
    font-weight: 700;
    letter-spacing: 0.3px;
    line-height: 18px;
  }
  .person-name .first { color: var(--teal); }
  .person-name .last { color: var(--green); }
  .person-title { margin: 0 0 6px; font-size: 12.5px; line-height: 16px; }
  .contact-list { list-style: none; margin: 0; padding: 0; }
  .contact-list li {
    display: flex;
    align-items: center;
    gap: 3px;
    font-size: 12.5px;
    line-height: 16px;
  }
  .contact-icon { width: 13px; height: 13px; flex: none; }
  .company {
    margin: 9px 0 1px;
    color: var(--green);
    font-size: 11px;
    font-weight: 700;
    letter-spacing: 0.5px;
  }
  .address { margin: 0; font-size: 12.5px; line-height: 16px; font-style: normal; }

  .back-pattern {
    position: absolute;
    inset: 0;
    background: radial-gradient(ellipse at 55% 50%, var(--teal) 0%, #3fbfbd 45%, var(--green) 100%);
  }
  .back-mark {
    position: absolute;
    left: 282px;
    top: 140px;
    display: flex;
    align-items: center;
    gap: 8px;
  }
  .back-mark-circle {
    width: 54px;
    height: 54px;
    border: 2.5px solid #ffffff;
    border-radius: 50%;
    box-sizing: border-box;
  }
  .back-mark-name {
    color: #ffffff;
    font-size: 15px;
    font-weight: 400;
    letter-spacing: 0.5px;
  }
</style>
</head>
<body>
<div class="canvas">
  <section class="card card-front">
    <div class="brand">
      <span class="brand-circle"></span>
      <p class="brand-name">Corvane<br>Therapeutics</p>
    </div>
    <div class="divider"></div>
    <div class="contact">
      <h1 class="person-name"><span class="first">DANIEL</span> <span class="last">MARSH</span></h1>
      <p class="person-title">Senior Director of Marketing</p>
      <ul class="contact-list">
        <li>
          <svg class="contact-icon" viewBox="0 0 14 14" aria-hidden="true">
            <circle cx="7" cy="7" r="6.3" fill="var(--icon-fill)" stroke="var(--teal)" stroke-width="0.9"/>
            <path d="M4.2 5.6c0-.8 1.3-1.3 2.8-1.3s2.8.5 2.8 1.3v.6H8.6v-.7H5.4v.7H4.2z M4.6 9.6l1-2.6h2.8l1 2.6z" fill="var(--teal)"/>
          </svg>
          555-214-0387
        </li>
        <li>
          <svg class="contact-icon" viewBox="0 0 14 14" aria-hidden="true">
            <circle cx="7" cy="7" r="6.3" fill="var(--icon-fill)" stroke="var(--teal)" stroke-width="0.9"/>
            <rect x="5" y="3.6" width="4" height="6.8" rx="0.8" fill="none" stroke="var(--teal)" stroke-width="0.9"/>
          </svg>
          555-362-7140
        </li>
        <li>
          <svg class="contact-icon" viewBox="0 0 14 14" aria-hidden="true">
            <circle cx="7" cy="7" r="6.3" fill="var(--icon-fill)" stroke="var(--teal)" stroke-width="0.9"/>
            <rect x="4" y="5" width="6" height="4.2" fill="var(--teal)"/>
            <path d="M4 5l3 2.4L10 5" fill="none" stroke="#ffffff" stroke-width="0.7"/>
          </svg>
          dmarsh@corvanerx.com
        </li>
      </ul>
      <p class="company">CORVANE THERAPEUTICS, LLC</p>
      <address class="address">118 W Clayton Street<br>Marlow, GA 30512</address>
    </div>
  </section>

  <section class="card card-back">
    <div class="back-pattern" role="img" aria-label="Teal-to-green gradient with a faint repeating brand-mark pattern"></div>
    <div class="back-mark">
      <span class="back-mark-circle"></span>
      <span class="back-mark-name">Corvane</span>
    </div>
  </section>
</div>
</body>
</html>
```